Website Design for a holiday home letting busines

We require a redesign of our present website www.pinebrookstays.com. We want the website to stand out and look professional and clean to make holiday hunters want to book a caravan or lodge holiday with us. Our logo is red however we DO NOT want the website to be red. We want a natural colour scheme.

The final design should communicate that we are a professional company to book with.

On the home page we require;
Overview of company
Photo
Search box for holiday (check in)
Late Deals
Reviews
News

We would like the following pages designed; home page, available dates page, caravans page, content page.

The website should be responsive for smart phones. One website I do like is http://www.verdoliso.be/nl/

Target Market(s)

Families

Industry/Entity Type

Travel

Number of Pages Required

5+ page

Font styles to use
Serif

Requirements
Must have
• The project must be responsive for mobile phones and tablets.
• Ability to search for holiday home holidays
• We want a natural colour scheme.
Nice to have
• A style we like is http://www.verdoliso.be/nl/
Should not have
• Do not use red as a colour for the website. Our logo is red so this is the only time we want this used.

```html
<!DOCTYPE html>
<html lang="en">
<head>
<meta charset="utf-8">
<title>Pinebrook Stays – Private Holiday Rentals</title>
<link href="https://fonts.googleapis.com/css2?family=Open+Sans:ital,wght@0,400;0,600;0,700;1,400&family=Montserrat:wght@600;700&display=swap" rel="stylesheet">
<style>
:root{
  --navy:#1e3552;
  --navy-light:#2c4b70;
  --blue:#2b78b9;
  --blue-dark:#21619a;
  --ink:#333a42;
  --muted:#7b848d;
  --line:#dde3e8;
  --tint:#e4eef6;
  --tint2:#eef3f7;
  --panel:#2c3036;
  --foot:#2a2c30;
  --foot-dark:#1f2023;
  --brand:#c9262c;
  --star:#e3a81b;
  --white:#fff;
}
*{box-sizing:border-box;margin:0;padding:0}
html,body{width:1200px;height:2628px;overflow:hidden}
body{font-family:"Open Sans",Arial,sans-serif;color:var(--ink);background:var(--white);font-size:13px;line-height:1.6}
.wrap{width:1120px;margin:0 auto;position:relative}
h1,h2,h3,h4{font-family:"Montserrat",Arial,sans-serif;font-weight:700}
.btn{display:inline-block;background:var(--blue);color:#fff;font-family:"Montserrat",Arial,sans-serif;font-size:11px;font-weight:600;letter-spacing:.5px;padding:9px 20px;border-radius:2px}
.more{color:var(--blue);font-size:11px;font-weight:700;text-transform:uppercase}

/* header */
.topbar{height:124px}
.topbar .wrap{height:124px}
.brand{position:absolute;left:0;top:28px;display:flex;align-items:center;gap:12px}
.brand-dot{width:46px;height:46px;border-radius:50%;background:var(--brand)}
.brand-name{font-size:26px;font-weight:700;color:#3a3f45;line-height:1.1}
.brand-tag{font-size:11px;color:var(--muted)}
.contact{position:absolute;right:0;top:16px;display:flex;gap:26px;font-size:12px;color:var(--muted)}
.contact span{display:flex;align-items:center;gap:6px}
.search{position:absolute;right:0;top:48px;width:230px;height:32px;border:1px solid var(--line);border-radius:2px;font-size:11px;color:#aab;padding:6px 10px}
.search svg{position:absolute;right:9px;top:9px}
.nav{background:var(--navy);height:32px}
.nav ul{list-style:none;display:flex;height:32px}
.nav li{color:#fff;font-size:10.5px;font-weight:700;padding:0 17px;line-height:32px;text-transform:uppercase;font-family:"Montserrat",Arial,sans-serif}
.nav li.active{background:var(--blue)}
.nav li:last-child{margin-left:auto}

/* hero */
.hero{height:484px;position:relative;background:linear-gradient(180deg,#6fb4e2 0%,#a9d6ef 38%,#5fb7d2 55%,#2d8fae 75%,#6d4b34 88%,#8a5c3c 100%)}
.hero-copy{position:absolute;left:584px;top:152px;color:#fff;width:520px}
.hero-copy h1{font-size:38px;letter-spacing:.5px;line-height:1.1}
.hero-copy p{font-size:14px;font-weight:600;margin-top:10px;letter-spacing:.3px;text-transform:uppercase}
.hero-btns{margin-top:28px;display:flex;gap:30px}
.hero-btns .btn{padding:11px 28px}
.hero-btns .ghost{background:transparent;border:2px solid #fff}

/* welcome */
.welcome{height:290px}
.welcome .wrap{height:290px}
.intro{position:absolute;left:0;top:30px;width:740px}
.intro h2{font-size:19px;color:#2f353c}
.intro .sub{font-style:italic;color:var(--blue);font-size:12px;margin-bottom:14px}
.intro p{font-size:11.5px;color:#555d66;margin-bottom:8px}
.booker{position:absolute;right:0;top:-36px;width:330px;height:250px;background:var(--panel);padding:18px 24px;color:#fff}
.booker h3{font-size:14px;text-align:center;letter-spacing:.5px;padding-bottom:12px;border-bottom:1px solid #454a52;margin-bottom:18px}
.field{background:#fff;color:#777;font-size:11px;height:32px;padding:7px 12px;margin-bottom:12px;position:relative}
.field svg{position:absolute;right:10px;top:9px}
.booker .btn{display:block;width:150px;margin:18px auto 0;text-align:center}

/* section titles */
.title{text-align:center;font-size:20px;color:#2f353c;display:flex;align-items:center;justify-content:center;gap:22px}
.title::before,.title::after{content:"";width:150px;height:1px;background:#c6cfd6}
.arrow{position:absolute;width:26px;height:40px;background:#fff;display:flex;align-items:center;justify-content:center;border:1px solid var(--line)}

/* caravans */
.fleet{background:var(--tint);height:326px;padding-top:30px}
.fleet-row{display:flex;gap:30px;margin:26px 60px 0}
.unit{width:227px;text-align:center}
.unit .ph{height:140px;border:4px solid #fff}
.unit h4{font-size:12px;margin-top:10px;color:#2f353c}
.stars{color:var(--star);font-size:13px;letter-spacing:1px}

/* deals */
.deals{height:450px;padding-top:36px}
.deal-row{display:flex;gap:42px;margin:28px 50px 0}
.deal{width:326px;border:1px solid var(--line);background:#fff}
.deal .ph{height:150px}
.deal .body{padding:12px 16px 16px}
.deal h4{font-size:11.5px;color:#2f353c;line-height:1.4}
.meta{display:flex;justify-content:space-between;font-size:10px;color:var(--muted);border-bottom:1px solid var(--line);padding:4px 0}
.price{font-size:20px;font-weight:700;color:#2f353c;margin:8px 0}

/* reviews + blog */
.news{background:var(--tint2);height:480px;padding-top:30px}
.news .wrap{display:flex;gap:60px}
.col-l{width:530px}.col-r{width:530px}
.col-h{font-size:18px;color:#2f353c;margin-bottom:16px}
.review{background:#fff;padding:16px 20px;margin-bottom:18px;border:1px solid var(--line)}
.review h4{font-size:11px;color:#2f353c}
.review .stay{font-size:10px;color:var(--blue);font-style:italic}
.review p{font-size:11px;color:#666;margin:6px 0}
.post{display:flex;gap:16px;margin-bottom:20px}
.post .ph{width:96px;height:70px;flex:none}
.post h4{font-size:11px;color:#2f353c;line-height:1.45;text-transform:uppercase}
.post .date{font-size:10px;color:var(--muted)}

/* footer */
.footer{background:var(--foot);color:#c8cdd2;height:388px;padding-top:30px}
.footer .wrap{display:flex;gap:40px}
.fcol{width:250px}
.fcol h4{color:#fff;font-size:13px;margin-bottom:16px;letter-spacing:.5px}
.friend{display:flex;gap:10px;margin-bottom:14px;font-size:10px}
.friend .av{width:40px;height:40px;background:#5c6268;flex:none}
.friend b{color:#fff;font-size:11px;display:block}
.fcol p{font-size:11px;margin-bottom:12px}
.input{background:#fff;color:#888;height:30px;font-size:11px;padding:6px 10px;width:200px;margin-bottom:10px}
.social{display:flex;align-items:center;gap:12px;margin-bottom:14px;font-size:11px}
.social i{width:32px;height:32px;border-radius:50%;background:#464a50;display:block}
.cinfo{font-size:11px;display:flex;gap:10px;margin-bottom:10px}
.fcol.contactcol h4{color:#4d9ad6;font-size:16px}
.legal{background:var(--foot);border-top:1px solid #3a3d42;height:88px;text-align:center;font-size:10.5px;color:#a7adb3;padding-top:22px;position:relative}
.chat{position:absolute;right:40px;bottom:0;background:#3b3f45;color:#fff;font-size:11px;font-weight:700;padding:8px 22px}
</style>
</head>
<body>

<header class="topbar">
  <div class="wrap">
    <div class="brand">
      <div class="brand-dot"></div>
      <div>
        <div class="brand-name">Pinebrook Stays</div>
        <div class="brand-tag">on Ashcombe Bay Holiday Park</div>
      </div>
    </div>
    <div class="contact">
      <span><svg width="12" height="12" viewBox="0 0 24 24"><path fill="#7b848d" d="M6.6 10.8a15 15 0 006.6 6.6l2.2-2.2c.3-.3.7-.4 1-.2 1.1.4 2.3.6 3.6.6.6 0 1 .4 1 1V20c0 .6-.4 1-1 1A17 17 0 013 4c0-.6.4-1 1-1h3.5c.6 0 1 .4 1 1 0 1.2.2 2.4.6 3.6.1.3 0 .7-.2 1z"/></svg>01632 960 418</span>
      <span><svg width="13" height="11" viewBox="0 0 26 20"><rect x="1" y="1" width="24" height="18" fill="none" stroke="#7b848d" stroke-width="2"/><path d="M1 1l12 10L25 1" fill="none" stroke="#7b848d" stroke-width="2"/></svg>info@pinebrookstays.com</span>
    </div>
    <div class="search">Search...
      <svg width="13" height="13" viewBox="0 0 24 24"><circle cx="10" cy="10" r="7" fill="none" stroke="#999" stroke-width="2.5"/><path d="M15 15l7 7" stroke="#999" stroke-width="2.5"/></svg>
    </div>
  </div>
</header>

<nav class="nav">
  <div class="wrap">
    <ul>
      <li class="active">Home</li><li>News &amp; Reviews</li><li>Caravans &amp; Lodges</li><li>Offer Holidays</li><li>Payment Plans</li><li>Ashcombe Bay</li><li>Local Attractions</li><li>Contact Us</li>
    </ul>
  </div>
</nav>

<section class="hero" role="img" aria-label="Photo of wooden holiday lodges with a deck above a turquoise sea under a blue sky">
  <div class="hero-copy">
    <h1>PRIVATE HOLIDAY RENTALS</h1>
    <p>Quality lodge &amp; caravan hire at Ashcombe Bay<br>Holiday Park. Book online today!</p>
    <div class="hero-btns"><span class="btn">BOOK HERE</span><span class="btn ghost">READ MORE</span></div>
  </div>
</section>

<section class="welcome">
  <div class="wrap">
    <div class="intro">
      <h2>WELCOME TO PINEBROOK STAYS</h2>
      <div class="sub">Quality Lodge &amp; Caravan Hire at Ashcombe Bay Holiday Park</div>
      <p>We have hand-picked a range of family friendly caravans and lodges on the park so every guest enjoys a clean, well kept and comfortable home from home. Each one is checked before you arrive and comes fully equipped for a relaxing stay.</p>
      <p>Our friendly team is here to help you plan the perfect short break or longer holiday. Choose your dates, pick the unit that suits your family and book in minutes with a secure deposit and easy payment plan.</p>
      <p>Guests can enjoy the pools, play areas and evening entertainment, with the beach and countryside only a short drive away.</p>
      <span class="more">Read more</span>
    </div>
    <div class="booker">
      <h3>BOOK YOUR VACATION</h3>
      <div class="field">CHECK - IN<svg width="14" height="14" viewBox="0 0 24 24"><rect x="3" y="5" width="18" height="16" fill="none" stroke="#888" stroke-width="2"/><path d="M3 10h18M8 2v5M16 2v5" stroke="#888" stroke-width="2"/></svg></div>
      <div class="field">CHECK - OUT<svg width="14" height="14" viewBox="0 0 24 24"><rect x="3" y="5" width="18" height="16" fill="none" stroke="#888" stroke-width="2"/><path d="M3 10h18M8 2v5M16 2v5" stroke="#888" stroke-width="2"/></svg></div>
      <span class="btn">BOOK YOUR HOLIDAY</span>
    </div>
  </div>
</section>

<section class="fleet">
  <div class="wrap">
    <h2 class="title">LIST OF CARAVANS AND LODGES</h2>
    <div class="arrow" style="left:0;top:110px"><svg width="8" height="12"><path d="M7 1L2 6l5 5" fill="none" stroke="#555" stroke-width="2"/></svg></div>
    <div class="arrow" style="right:0;top:110px"><svg width="8" height="12"><path d="M1 1l5 5-5 5" fill="none" stroke="#555" stroke-width="2"/></svg></div>
    <div class="fleet-row">
      <div class="unit"><div class="ph" role="img" aria-label="Photo of a caravan bedroom" style="background:linear-gradient(135deg,#c9b59a,#8e7a63)"></div><h4>THE HARTWELL</h4><div class="stars">★★★★★</div></div>
      <div class="unit"><div class="ph" role="img" aria-label="Photo of a caravan lounge" style="background:linear-gradient(135deg,#d8cbb6,#9d8b74)"></div><h4>THE LINFORD</h4><div class="stars">★★★★★</div></div>
      <div class="unit"><div class="ph" role="img" aria-label="Photo of a lodge living area" style="background:linear-gradient(135deg,#c2a98c,#7f6a55)"></div><h4>THE ASHBY</h4><div class="stars">★★★★★</div></div>
      <div class="unit"><div class="ph" role="img" aria-label="Photo of a caravan kitchen and lounge" style="background:linear-gradient(135deg,#d3c0a4,#94806a)"></div><h4>THE MARLOW</h4><div class="stars">★★★★★</div></div>
    </div>
  </div>
</section>

<section class="deals">
  <div class="wrap">
    <h2 class="title">LATE DEALS</h2>
    <div class="arrow" style="left:0;top:170px"><svg width="8" height="12"><path d="M7 1L2 6l5 5" fill="none" stroke="#555" stroke-width="2"/></svg></div>
    <div class="arrow" style="right:0;top:170px"><svg width="8" height="12"><path d="M1 1l5 5-5 5" fill="none" stroke="#555" stroke-width="2"/></svg></div>
    <div class="deal-row">
      <div class="deal"><div class="ph" role="img" aria-label="Photo of a caravan lounge" style="background:linear-gradient(135deg,#cdbba2,#8b7862)"></div>
        <div class="body"><h4>THE SEAVIEW FRIDAY 18 SEPTEMBER 2015 (3 NIGHTS)</h4>
          <div class="meta"><span>Price: £149</span><span>Sleeps: 6</span></div><div class="meta"><span>Nights: 3</span><span>Pets: No</span></div>
          <div class="price">£149.00</div><span class="btn">BOOK NOW</span></div></div>
      <div class="deal"><div class="ph" role="img" aria-label="Photo of a lodge interior" style="background:linear-gradient(135deg,#d6c6ad,#9a856c)"></div>
        <div class="body"><h4>THE ASHBY FRIDAY 18 SEPTEMBER 2015 (3 NIGHTS)</h4>
          <div class="meta"><span>Price: £149</span><span>Sleeps: 6</span></div><div class="meta"><span>Nights: 3</span><span>Pets: No</span></div>
          <div class="price">£149.00</div><span class="btn">BOOK NOW</span></div></div>
      <div class="deal"><div class="ph" role="img" aria-label="Photo of a caravan bedroom" style="background:linear-gradient(135deg,#c6b196,#85715b)"></div>
        <div class="body"><h4>THE SEAVIEW FRIDAY 11 SEPTEMBER 2015 (3 NIGHTS)</h4>
          <div class="meta"><span>Price: £149</span><span>Sleeps: 6</span></div><div class="meta"><span>Nights: 3</span><span>Pets: No</span></div>
          <div class="price">£149.00</div><span class="btn">BOOK NOW</span></div></div>
    </div>
  </div>
</section>

<section class="news">
  <div class="wrap">
    <div class="col-l">
      <h2 class="col-h">LATEST REVIEWS</h2>
      <div class="review"><h4>CARLA DENHOLM</h4><div class="stay">Stayed in The Linford</div>
        <p>Lovely clean caravan with everything we needed for our family week. The kids loved the pool and the staff were so helpful. We will be booking again next summer.</p><span class="more">Read more</span></div>
      <div class="review"><h4>IRENE MALCOTT</h4><div class="stay">Stayed in The Hartwell</div>
        <p>Booking was quick and easy and the lodge was spotless on arrival. Great location on the park, close to the beach path. A relaxing break for all of us.</p><span class="more">Read more</span></div>
    </div>
    <div class="col-r">
      <h2 class="col-h">OUR BLOG</h2>
      <div class="post"><div class="ph" role="img" aria-label="Photo of the holiday park" style="background:linear-gradient(135deg,#9cc1d9,#5f8aa6)"></div><div><h4>New family lodges arrive on the park for the summer season</h4><div class="date">12 July 2015</div><span class="more">Read more</span></div></div>
      <div class="post"><div class="ph" role="img" aria-label="Photo of the beach" style="background:linear-gradient(135deg,#a8cbe0,#6a94ae)"></div><div><h4>Top five days out near the coast for young families</h4><div class="date">02 July 2015</div><span class="more">Read more</span></div></div>
      <div class="post"><div class="ph" role="img" aria-label="Photo of the pool" style="background:linear-gradient(135deg,#95bcd6,#58839f)"></div><div><h4>Autumn short breaks now open for online booking</h4><div class="date">24 June 2015</div><span class="more">Read more</span></div></div>
      <div class="post"><div class="ph" role="img" aria-label="Photo of countryside walks" style="background:linear-gradient(135deg,#a2c6dc,#6690aa)"></div><div><h4>Our guide to payment plans and booking deposits</h4><div class="date">15 June 2015</div><span class="more">Read more</span></div></div>
    </div>
  </div>
</section>

<footer>
  <div class="footer">
    <div class="wrap">
      <div class="fcol">
        <h4>COMMUNITY</h4>
        <div class="friend"><div class="av" role="img" aria-label="Profile picture"></div><div><b>Nina Farrow</b>17 August at 18:02<br>Lovely stay, thank you</div></div>
        <div class="friend"><div class="av" role="img" aria-label="Profile picture"></div><div><b>Tessa Rowley</b>17 August at 11:40<br>Booked again for May</div></div>
      </div>
      <div class="fcol">
        <h4>SUBSCRIBE OUR NEWSLETTER</h4>
        <p>Register your email below to get our latest deals and park news.</p>
        <div class="input">Enter your email</div>
        <span class="btn">SIGN UP</span>
      </div>
      <div class="fcol" style="width:200px">
        <h4>FOLLOW US ON</h4>
        <div class="social"><i></i>Our page</div>
        <div class="social"><i></i>Our feed</div>
        <div class="social"><i></i>Photos</div>
      </div>
      <div class="fcol contactcol">
        <h4>Contact Us</h4>
        <div class="cinfo"><svg width="12" height="14" viewBox="0 0 24 28"><path fill="#c8cdd2" d="M12 0a9 9 0 00-9 9c0 7 9 19 9 19s9-12 9-19a9 9 0 00-9-9zm0 13a4 4 0 110-8 4 4 0 010 8z"/></svg><span>Pinebrook Stays Ltd, 14 Harbour Lane,<br>Ashcombe Bay Holiday Park, AB1 2CD</span></div>
        <div class="cinfo"><svg width="12" height="12" viewBox="0 0 24 24"><path fill="#c8cdd2" d="M6.6 10.8a15 15 0 006.6 6.6l2.2-2.2c.3-.3.7-.4 1-.2 1.1.4 2.3.6 3.6.6.6 0 1 .4 1 1V20c0 .6-.4 1-1 1A17 17 0 013 4c0-.6.4-1 1-1h3.5c.6 0 1 .4 1 1 0 1.2.2 2.4.6 3.6.1.3 0 .7-.2 1z"/></svg>01632 960 418</div>
        <div class="cinfo"><svg width="12" height="12" viewBox="0 0 24 24"><path fill="#c8cdd2" d="M6.6 10.8a15 15 0 006.6 6.6l2.2-2.2c.3-.3.7-.4 1-.2 1.1.4 2.3.6 3.6.6.6 0 1 .4 1 1V20c0 .6-.4 1-1 1A17 17 0 013 4c0-.6.4-1 1-1h3.5c.6 0 1 .4 1 1 0 1.2.2 2.4.6 3.6.1.3 0 .7-.2 1z"/></svg>07700 900 215</div>
        <div class="cinfo"><svg width="13" height="11" viewBox="0 0 26 20"><rect x="1" y="1" width="24" height="18" fill="none" stroke="#c8cdd2" stroke-width="2"/><path d="M1 1l12 10L25 1" fill="none" stroke="#c8cdd2" stroke-width="2"/></svg>info@pinebrookstays.com</div>
      </div>
    </div>
  </div>
  <div class="legal">
    Privacy Policy &nbsp;|&nbsp; Terms and Conditions &nbsp;|&nbsp; Contact Us<br>
    Pinebrook Stays © 2015. All rights reserved.
    <span class="chat">LIVE CHAT</span>
  </div>
</footer>

</body>
</html>
```